Velvet Lantern rebranding my business with a new business card

I have my new logo and now I need a refresher on my business cards. I really want something fun and fresh. I like black background or anything to make the color pop.
Logo
Name: Velvet Lantern
Contact Info as stated below:
Mira Pellow
555-013-4762
Logo
Name: Velvet Lantern
Mira Pellow
555-013-4762
fb.me/VelvetLanternbyMira
Instagram: @VelvetLanternbyMira

Industry/Entity Type

Business

Contact Information for Business Card

double-sided. Logo on one side. Contact info on the other.

Requirements
Must have
• Logo
• Name: Velvet Lantern
• Contact Info as stated below:
• Mira Pellow
• 555-013-4762
• fb.me/VelvetLanternbyMira
• fb.me/VelvetLanternbyMira

```html
<!DOCTYPE html>
<html lang="en">
<head>
<meta charset="utf-8">
<title>Velvet Lantern — Business Card</title>
<link rel="stylesheet" href="https://fonts.googleapis.com/css2?family=Zilla+Slab:wght@400;500;600&display=swap">
<style>
  :root {
    --backdrop: #e4e4e4;
    --card-white: #ffffff;
    --teal: #35b8a2;
    --teal-deep: #15b09a;
    --teal-text: #2aa990;
    --grey-text: #5f5f5f;
    --ring-pink: #f1a9bd;
    --ring-dark: #2b2b2b;
  }
  html, body {
    margin: 0;
    padding: 0;
    width: 1200px;
    height: 1000px;
    overflow: hidden;
    background: var(--backdrop);
    font-family: "Zilla Slab", Georgia, serif;
  }
  .canvas {
    position: relative;
    width: 1200px;
    height: 1000px;
  }
  .card {
    position: absolute;
    left: 239px;
    width: 698px;
    height: 398px;
    border-radius: 18px;
    overflow: hidden;
  }
  .card--front {
    top: 82px;
    background: var(--card-white);
  }
  .card--back {
    top: 520px;
    background: var(--teal-deep);
  }
  .front-band {
    position: absolute;
    left: 0;
    top: 0;
    width: 100%;
    height: 96px;
    background: var(--teal);
  }
  .brand-badge {
    position: absolute;
    border-radius: 50%;
    background: var(--card-white);
    box-shadow: 0 0 0 1.5px var(--ring-dark), inset 0 0 0 5px var(--card-white), inset 0 0 0 6.5px var(--ring-pink);
    display: flex;
    align-items: center;
    justify-content: center;
    text-align: center;
  }
  .brand-badge--front {
    left: 80px;
    top: 61px;
    width: 156px;
    height: 156px;
  }
  .brand-badge--back {
    left: 248px;
    top: 97px;
    width: 204px;
    height: 204px;
  }
  .brand-name {
    font-weight: 600;
    color: var(--teal-text);
    letter-spacing: 1px;
    line-height: 1.1;
    text-transform: uppercase;
  }
  .brand-badge--front .brand-name { font-size: 20px; }
  .brand-badge--back .brand-name { font-size: 26px; }
  .holder {
    position: absolute;
    right: 78px;
    top: 144px;
    text-align: right;
  }
  .holder-name {
    margin: 0;
    font-size: 31px;
    font-weight: 500;
    letter-spacing: 2.5px;
    color: var(--teal-text);
    text-transform: uppercase;
    line-height: 1;
  }
  .holder-title {
    margin: 4px 0 0;
    font-size: 17px;
    letter-spacing: 1.5px;
    color: var(--grey-text);
    font-variant: small-caps;
    line-height: 1;
  }
  .contact-line {
    position: absolute;
    left: 0;
    right: 0;
    top: 349px;
    margin: 0;
    text-align: center;
    font-size: 17.5px;
    color: var(--teal-text);
    letter-spacing: 0.4px;
  }
  .back-pattern {
    position: absolute;
    inset: 0;
    background: var(--teal-deep);
  }
</style>
</head>
<body>
  <main class="canvas">
    <section class="card card--front">
      <div class="front-band"></div>
      <div class="brand-badge brand-badge--front">
        <span class="brand-name">Velvet<br>Lantern</span>
      </div>
      <div class="holder">
        <h1 class="holder-name">Mira Pellow</h1>
        <p class="holder-title">Owner</p>
      </div>
      <p class="contact-line">555-013-4762 | info@mirapellow.com | me/VelvetLanternbyMira</p>
    </section>

    <section class="card card--back">
      <div class="back-pattern" role="img" aria-label="Scattered confetti dots in pink, yellow and violet on teal"></div>
      <div class="brand-badge brand-badge--back">
        <span class="brand-name">Velvet<br>Lantern</span>
      </div>
    </section>
  </main>
</body>
</html>
```